Digital Marketing Agency Landing Page

At VELIM, we offer a comprehensive solution for solar companies' client acquisition needs in the rapidly growing industry. We handle end-to-end client acquisition, meaning we manage the entire lifecycle of capturing new clients—from initial lead generation to delivering the ready-to-buy homeowner. Our expertise in targeted advertising, data analytics, and customer relationship management ensures that we not only find potential customers but also nurture them through tailored engagement strategies until they are ready to make a purchase. By entrusting us with your client acquisition process, solar companies can focus on what they do best—providing sustainable energy solutions—while we work behind the scenes to grow your customer base and increase your market share.

We need to restructure our website to make it more professional. We don't need any complex functionalities. We are looking for someone that is good in design and can build a visually aesthetic website following our brand image. We only need a landing page and a lead form in the end. I would like to have only one page, but a relatively big one where people scroll down. I would like to have a minimal and classy look. Something that is timeless and elegant.

Structure:

initial page
About us
How we operate
Get in touch

Target Market(s)

Solar Comapanies

Industry/Entity Type

Marketing solautions

Coding

Coded - Design and coding required

Number of Pages Required

1 page

Requirements
Nice to have
• Inspirations: https://www.qz.zu/ https://www.marchbeck.example/ https://www.tovanrid.example/ https://pruvo.example/

```html
<!DOCTYPE html>
<html lang="en">
<head>
<meta charset="utf-8">
<title>VELIM — Client Acquisition for Solar Companies</title>
<link href="https://fonts.googleapis.com/css2?family=Montserrat:wght@300;400;500;600&family=Manrope:wght@400;500;600&display=swap" rel="stylesheet">
<style>
:root{
  --ink:#0f1f2c;
  --navy:#14253a;
  --field:#e6e7e9;
  --white:#ffffff;
  --hero-a:#23408e;
  --hero-b:#1d1f63;
  --hero-c:#250f3f;
  --text:#1c2530;
}
*{margin:0;padding:0;box-sizing:border-box}
html,body{width:1200px;height:2173px;overflow:hidden;background:var(--white)}
body{position:relative;font-family:"Manrope",sans-serif;color:var(--text)}
.abs{position:absolute}
.brand{border:1px solid var(--ink);display:flex;align-items:center;justify-content:center;font-family:"Montserrat",sans-serif;font-weight:300;letter-spacing:1px}
.brand::after{content:"";position:absolute;inset:4px -4px -4px 4px;border:1px solid var(--ink)}
.site-header .brand{left:110px;top:13px;width:151px;height:58px;font-size:33px;color:var(--ink)}
.nav a{position:absolute;top:35px;font-family:"Montserrat",sans-serif;font-weight:500;font-size:15px;color:var(--ink);text-decoration:none;letter-spacing:.3px}
.search{left:1045px;top:29px;width:44px;height:35px;background:var(--ink);display:flex;align-items:center;justify-content:center}
.hero-band{left:0;top:86px;width:1168px;height:590px;background:linear-gradient(100deg,var(--hero-a) 0%,var(--hero-b) 55%,var(--hero-c) 100%)}
.hero-band-edge{left:1168px;top:118px;width:32px;height:558px;background:var(--hero-c)}
.hero-art{left:30px;top:86px;width:630px;height:590px;background:radial-gradient(ellipse at 50% 55%,#3c5cff 0%,#2a3fb8 35%,#1d2a86 70%,rgba(29,31,99,0) 100%)}
.quote-card{left:660px;top:162px;width:495px;height:561px;background:var(--white);border-radius:17px;box-shadow:0 4px 18px rgba(15,31,44,.18)}
.quote-card h2{position:absolute;top:40px;width:100%;text-align:center;font-family:"Montserrat",sans-serif;font-weight:500;font-size:26px;color:var(--ink);letter-spacing:.5px}
.field{position:absolute;left:41px;width:412px;height:56px;background:var(--field);font-family:"Manrope",sans-serif;font-weight:600;font-size:15px;color:var(--ink);padding:0 24px;display:flex;align-items:center}
.field.message{align-items:flex-start;padding-top:20px;height:101px}
.submit{position:absolute;left:180px;top:465px;width:135px;height:55px;background:var(--ink);color:var(--white);font-family:"Montserrat",sans-serif;font-weight:600;font-size:19px;display:flex;align-items:center;justify-content:center;letter-spacing:.5px}
.section-title{width:1200px;text-align:center;font-family:"Montserrat",sans-serif;font-weight:500;color:var(--ink);letter-spacing:.5px}
.service{background:var(--white);box-shadow:0 0 10px rgba(15,31,44,.13);text-align:center}
.service.featured{box-shadow:none;border:1.5px solid var(--ink)}
.service-frame{left:439px;top:857px;width:315px;height:334px;border:1.5px solid var(--ink);border-right:none;border-bottom:none}
.service-frame::after{content:"";position:absolute;right:0;top:0;width:0}
.service svg.icon{position:absolute;left:50%;top:18px;transform:translateX(-50%)}
.service h3{position:absolute;top:112px;width:100%;font-family:"Montserrat",sans-serif;font-weight:500;font-size:20.5px;color:var(--ink);white-space:nowrap}
.service p{position:absolute;top:154px;width:100%;font-size:15.5px;line-height:36px;color:var(--text)}
.go{width:44px;height:43px;background:var(--ink);display:flex;align-items:center;justify-content:center}
.about-frame{left:167px;top:1395px;width:406px;height:276px;border:2px solid var(--ink)}
.about-photo{left:159px;top:1417px;width:396px;height:266px;background:linear-gradient(180deg,#b9cfe2 0%,#8fa7b8 40%,#6a7a5e 68%,#9fb2cc 100%)}
.about-text{left:621px;top:1422px;width:440px;font-size:15.5px;line-height:36px;color:var(--text)}
.site-footer{left:0;top:1777px;width:1200px;height:396px;background:var(--ink);color:var(--white)}
.site-footer .brand{left:524px;top:51px;width:152px;height:58px;font-size:33px;color:var(--white);border-color:var(--white)}
.site-footer .brand::after{border-color:var(--white)}
.foot-nav a{position:absolute;top:147px;font-family:"Montserrat",sans-serif;font-weight:600;font-size:15.5px;color:var(--white);text-decoration:none}
.social{top:199px;width:41px;height:40px;background:#2f62a8}
.contact{top:257px;display:flex;align-items:center;gap:14px;font-weight:600;font-size:16px}
.contact .dot{width:51px;height:51px;border-radius:50%;background:var(--white);display:flex;align-items:center;justify-content:center}
.copyright{top:347px;width:1200px;text-align:center;font-size:13px;font-weight:500}
</style>
</head>
<body>

<header class="site-header">
  <div class="abs brand">VELIM</div>
  <nav class="nav">
    <a style="left:393px" href="#">HOME</a>
    <a style="left:486px" href="#about">ABOUT US</a>
    <a style="left:610px" href="#services">OUR SERVICES</a>
    <a style="left:770px" href="#quote">CONTACT US</a>
  </nav>
  <div class="abs search"><svg width="16" height="16" viewBox="0 0 16 16"><circle cx="6.5" cy="6.5" r="4.5" fill="none" stroke="#fff" stroke-width="1.6"/><line x1="10" y1="10" x2="14" y2="14" stroke="#fff" stroke-width="1.6"/></svg></div>
</header>

<section class="hero">
  <div class="abs hero-band"></div>
  <div class="abs hero-band-edge"></div>
  <div class="abs hero-art" role="img" aria-label="Illustration of a laptop showing a marketing dashboard with charts, surrounded by glowing blue rings of light"></div>
  <form class="abs quote-card" id="quote">
    <h2>GET A QUOTE</h2>
    <div class="field" style="top:108px">FULL NAME</div>
    <div class="field" style="top:183px">EMAIL ADDRESS</div>
    <div class="field" style="top:258px">PHONE NUMBER</div>
    <div class="field message" style="top:331px">ENTER YOUR MESSAGE...</div>
    <div class="submit">SUBMIT</div>
  </form>
</section>

<section id="services">
  <h2 class="abs section-title" style="top:783px;font-size:26px">OUR SERVICES</h2>

  <article class="abs service" style="left:111px;top:859px;width:312px;height:331px">
    <svg class="icon" width="74" height="74" viewBox="0 0 74 74" fill="none" stroke="#0f1f2c" stroke-width="2.5"><circle cx="32" cy="40" r="28"/><circle cx="32" cy="40" r="19"/><circle cx="32" cy="40" r="10"/><circle cx="32" cy="40" r="3"/><line x1="32" y1="40" x2="64" y2="8"/><path d="M56 10 L64 2 L66 8 L72 10 L64 18 Z"/></svg>
    <h3>TARGETED ADVERTISING</h3>
    <p>Nemo enim ipsam voluptatem quia<br>voluptas sit aspernatur aut odit<br>aut fugit, sed quia consequuntur<br>magni dolores eos qui ratione</p>
  </article>

  <div class="abs service-frame"></div>
  <article class="abs service featured" style="left:447px;top:866px;width:314px;height:334px">
    <svg class="icon" width="74" height="74" viewBox="0 0 74 74" fill="none" stroke="#0f1f2c" stroke-width="2.5" style="top:11px"><rect x="2" y="2" width="60" height="50" rx="3"/><rect x="8" y="8" width="60" height="50" rx="3"/><line x1="2" y1="12" x2="62" y2="12"/><line x1="16" y1="46" x2="16" y2="38"/><line x1="22" y1="46" x2="22" y2="32"/><line x1="28" y1="46" x2="28" y2="36"/><line x1="34" y1="46" x2="34" y2="26"/><line x1="40" y1="46" x2="40" y2="30"/><line x1="46" y1="46" x2="46" y2="22"/><circle cx="46" cy="46" r="13" fill="#fff"/><circle cx="46" cy="46" r="8"/><line x1="56" y1="56" x2="70" y2="70"/></svg>
    <h3>DATA ANALYTICS</h3>
    <p>Nemo enim ipsam voluptatem quia<br>voluptas sit aspernatur aut odit<br>aut fugit, sed quia consequuntur<br>magni dolores eos qui ratione</p>
  </article>

  <article class="abs service" style="left:775px;top:859px;width:312px;height:331px">
    <svg class="icon" width="74" height="74" viewBox="0 0 74 74" fill="none" stroke="#0f1f2c" stroke-width="2.5"><path d="M14 16 L10 10 M58 16 L62 10 M4 40 L10 40 M64 40 L70 40 M14 64 L10 70 M58 64 L62 70 M36 8 L36 14"/><circle cx="36" cy="40" r="26"/><circle cx="36" cy="40" r="19"/><polyline points="36,26 36,40 46,46"/><circle cx="56" cy="18" r="13" fill="#fff"/><polyline points="50,18 55,23 63,13"/></svg>
    <h3>CUSTOMER MANAGEMENT</h3>
    <p>Nemo enim ipsam voluptatem quia<br>voluptas sit aspernatur aut odit<br>aut fugit, sed quia consequuntur<br>magni dolores eos qui ratione</p>
  </article>

  <div class="abs go" style="left:246px;top:1168px"><svg width="26" height="26" viewBox="0 0 26 26"><circle cx="13" cy="13" r="12" fill="#fff"/><path d="M7 13 H18 M13 8 L18 13 L13 18" stroke="#0f1f2c" stroke-width="2.4" fill="none"/></svg></div>
  <div class="abs go" style="left:575px;top:1168px"><svg width="26" height="26" viewBox="0 0 26 26"><circle cx="13" cy="13" r="12" fill="#fff"/><path d="M7 13 H18 M13 8 L18 13 L13 18" stroke="#0f1f2c" stroke-width="2.4" fill="none"/></svg></div>
  <div class="abs go" style="left:909px;top:1168px"><svg width="26" height="26" viewBox="0 0 26 26"><circle cx="13" cy="13" r="12" fill="#fff"/><path d="M7 13 H18 M13 8 L18 13 L13 18" stroke="#0f1f2c" stroke-width="2.4" fill="none"/></svg></div>
</section>

<section id="about">
  <h2 class="abs section-title" style="top:1296px;font-size:31px">ABOUT US</h2>
  <div class="abs about-frame"></div>
  <div class="abs about-photo" role="img" aria-label="Photo of a handshake over a landscape of solar panels, wind turbines and mountains"></div>
  <p class="abs about-text">At VELIM, we offer a comprehensive solution for solar companies' client acquisition needs in the rapidly growing industry. We handle end-to-end client acquisition, meaning we manage the entire lifecycle of capturing new clients—from initial lead generation to delivering the ready-to-buy homeowner.</p>
</section>

<footer class="abs site-footer">
  <div class="abs brand">VELIM</div>
  <nav class="foot-nav">
    <a style="left:362px" href="#">HOME</a>
    <a style="left:454px" href="#about">ABOUT US</a>
    <a style="left:579px" href="#services">OUR SERVICES</a>
    <a style="left:738px" href="#quote">CONTACT US</a>
  </nav>
  <div class="abs social" style="left:556px" role="img" aria-label="Social profile"></div>
  <div class="abs social" style="left:603px;background:#0f6aa8" role="img" aria-label="Social profile"></div>

  <div class="abs contact" style="left:182px">
    <span class="dot"><svg width="24" height="24" viewBox="0 0 24 24"><path d="M5 2 L9 2 L11 7 L8 9 C9.5 12 12 14.5 15 16 L17 13 L22 15 L22 19 C22 20.5 20.5 22 19 22 C10 21 3 14 2 5 C2 3.5 3.5 2 5 2 Z" fill="#0f1f2c"/></svg></span>
    <span>+1 555 014 2290</span>
  </div>
  <div class="abs contact" style="left:447px">
    <span class="dot"><svg width="30" height="22" viewBox="0 0 30 22" fill="none" stroke="#0f1f2c" stroke-width="2.2"><rect x="1.5" y="1.5" width="27" height="19"/><polyline points="1.5,1.5 15,13 28.5,1.5"/><line x1="1.5" y1="20.5" x2="11" y2="10"/><line x1="28.5" y1="20.5" x2="19" y2="10"/></svg></span>
    <span>hello@velim.example</span>
  </div>
  <div class="abs contact" style="left:730px;gap:23px">
    <span class="dot"><svg width="20" height="28" viewBox="0 0 20 28"><path d="M10 1 C5 1 1 5 1 10 C1 17 10 27 10 27 C10 27 19 17 19 10 C19 5 15 1 10 1 Z" fill="#0f1f2c"/><circle cx="10" cy="10" r="3.5" fill="#fff"/></svg></span>
    <span>34, Velim, Lorem Ipsum Sit</span>
  </div>
  <p class="abs copyright">@2023 COPYRIGHTS. VELIM. ALL RIGHTS RESERVED.</p>
</footer>

</body>
</html>
```